Wedding Invitation to be used digitally

Design of a Wedding Invitation.
It will be used digitally by whatsapp, so the file format and image size should be appropriate. We don´t intend to print.
Word file with the text contents as attachment. This is REALLY just the text and the main sequencial order of the information that should appear in the invitation.
However, ALL criativity is welcome ofcourse in terms of organization of the information in the paper, font, uppercase and lowercase, numbers and their format, dates and their format, drawings, logo, etc etc

Target Market(s)

family and friends

Requirements
Must have
• A logo at the top with the capitals of our name - R and T
Nice to have
• Should be elegant

```html
<!DOCTYPE html>
<html lang="en">
<head>
<meta charset="UTF-8">
<title>Wedding Invitation – Rosa &amp; Tiago</title>
<link href="https://fonts.googleapis.com/css2?family=Playfair+Display:wght@400;500&display=swap" rel="stylesheet">
<style>
  :root {
    --backdrop: #efebec;
    --paper: #ffffff;
    --ink: #2e2c2c;
    --gold: #9a8660;
    --gold-line: #cdbb9c;
    --ampersand: #d6c6aa;
    --peony: #f3d6ea;
    --peony-soft: #f8e8f3;
  }
  * { margin: 0; padding: 0; box-sizing: border-box; }
  html, body {
    width: 1200px; height: 854px; overflow: hidden;
    background: var(--backdrop);
    font-family: "Playfair Display", Georgia, serif;
    color: var(--ink);
  }
  .invitation {
    position: absolute; left: 353px; top: 111px;
    width: 455px; height: 643px;
    background: var(--paper); overflow: hidden;
  }
  .florals {
    position: absolute; border-radius: 50%;
  }
  .florals--top {
    left: -40px; top: -50px; width: 330px; height: 230px;
    background: radial-gradient(ellipse at 40% 45%, var(--peony) 0%, var(--peony-soft) 55%, rgba(255,255,255,0) 72%);
  }
  .florals--bottom {
    left: 180px; top: 470px; width: 320px; height: 220px;
    background: radial-gradient(ellipse at 60% 55%, var(--peony) 0%, var(--peony-soft) 55%, rgba(255,255,255,0) 72%);
  }
  .frame {
    position: absolute; left: 31px; top: 107px; width: 392px; height: 472px;
    border: 1px solid var(--gold-line);
  }
  .monogram {
    position: absolute; left: 110px; top: 40px; width: 235px; height: 130px;
    display: flex; align-items: center; justify-content: center;
    background: var(--paper);
    font-size: 56px; font-weight: 400; color: var(--gold); letter-spacing: 4px;
    border-radius: 50%;
  }
  .line {
    position: absolute; left: 0; width: 100%; text-align: center; white-space: nowrap;
  }
  .eyebrow { font-size: 11px; letter-spacing: 2.2px; line-height: 12px; }
  .couple-name { font-size: 35px; line-height: 36px; font-weight: 400; letter-spacing: 0.5px; z-index: 2; }
  .ampersand {
    font-size: 100px; line-height: 100px; color: var(--ampersand); font-weight: 500; z-index: 1;
  }
  .rule {
    position: absolute; left: 197px; top: 397px; width: 61px; height: 1.5px; background: var(--gold);
  }
  .date { font-size: 15px; line-height: 17px; }
  .details { font-size: 10.5px; line-height: 13px; }
  .rsvp {
    position: absolute; left: 25px; top: 603px; font-size: 11.5px; letter-spacing: 1.5px;
  }
</style>
</head>
<body>
  <main class="invitation">
    <div class="florals florals--top" role="img" aria-label="Watercolour pink peonies with green leaves"></div>
    <div class="florals florals--bottom" role="img" aria-label="Watercolour pink peonies with green leaves"></div>
    <div class="frame"></div>
    <div class="monogram">R&amp;T</div>

    <p class="line eyebrow" style="top:221px">TOGETHER WITH THEIR FAMILIES</p>
    <p class="line ampersand" style="top:244px">&amp;</p>
    <h1 class="line couple-name" style="top:242px">ROSA LEMOS</h1>
    <h1 class="line couple-name" style="top:313px">TIAGO MOREIRA</h1>
    <p class="line eyebrow" style="top:365px">INVITE YOU TO THEIR WEDDING CELEBRATION</p>
    <div class="rule"></div>

    <p class="line date" style="top:413px">SUNDAY, JULY 28, 2024</p>
    <p class="line date" style="top:430px">AT 11h30</p>

    <p class="line details" style="top:460px">CAPELA DE SANTA LUZIA | CASCAIS</p>
    <p class="line details" style="top:473px">(PARKING – MARINA DO FAROL OR PARQUE TERRA AZUL)</p>
    <p class="line details" style="top:498px">RECEPTION TO FOLLOW</p>
    <p class="line details" style="top:524px">AT</p>
    <p class="line details" style="top:537px">HOTEL FORTE DA AREIA MAISON &amp; JARDINS | CASCAIS</p>
    <p class="line details" style="top:550px">(PARKING – ON SITE)</p>

    <p class="rsvp">RSVP BY 20TH JULY</p>
  </main>
</body>
</html>
```